Need a stunning home page for Car rental company

For a client, I need a slick and sumber home page design. It is a small, local car rental company, with a handful of cars available for rent.
Selling points: affordable lease, availability, always clean cars
The design should be:
- flat and modern
- no, or very few animations/sliders
- CTA: booking form for renting a car.
- 3 featured cars with images and facts (see website) with button to read more about the car.
- fullscreen background video can be an option
- main colour: #efba01
The site is under construction here:
http://solvikutleie.hammerlia.no/
Delivery requirements:
I need a layered & well organised PSD file delivered.

```html
<!DOCTYPE html>
<html lang="no">
<head>
<meta charset="utf-8">
<title>Solvik Utleie – Bilutleie</title>
<link rel="stylesheet" href="https://fonts.googleapis.com/css2?family=Open+Sans:wght@400;600;700&family=Roboto+Condensed:wght@400;700&display=swap">
<style>
:root{
  --gold:#e6b21a;
  --gold-dark:#c9960c;
  --ink:#333;
  --muted:#777;
  --line:#e4e4e4;
  --soft:#f5f5f5;
  --price:#d9651f;
  --red:#d23a2a;
  --dark:#1d1d1d;
}
*{box-sizing:border-box;margin:0;padding:0}
html,body{width:1200px;height:2192px;overflow:hidden}
body{position:relative;background:#fff;font-family:"Open Sans",sans-serif;color:var(--ink)}
.abs{position:absolute}
.center{left:0;width:1200px;text-align:center}

/* header */
.header{top:0;left:0;width:1200px;height:115px;background:#fafafa}
.brand{left:172px;top:34px;font-size:30px;font-weight:700;color:var(--gold);letter-spacing:1px;display:flex;align-items:center;gap:10px}
.brand-dot{width:14px;height:14px;border-radius:50%;background:var(--gold)}
.lang{left:658px;top:42px;width:142px;height:34px;border:1px solid var(--line);background:#fff;font-size:13px;display:flex;align-items:center;padding-left:10px;gap:10px}
.flag{width:26px;height:16px;background:linear-gradient(#b22 0 50%,#fff 50% 60%,#b22 60%);position:relative}
.flag:before{content:"";position:absolute;left:0;top:0;width:11px;height:9px;background:#3b4a8c}
.phone-ico{left:830px;top:38px}
.phone-txt{left:893px;top:34px;font-size:14px;line-height:25px;color:#555}

/* nav */
.nav{top:115px;left:0;width:1200px;height:54px;border-top:1px solid var(--line);border-bottom:1px solid var(--line);background:#fff}
.nav a{position:absolute;top:0;height:52px;line-height:52px;font-size:13px;color:#555;text-decoration:none;letter-spacing:.3px}
.nav a.active{background:var(--gold);color:#fff;padding:0 15px;left:172px}

/* hero */
.hero{top:169px;left:0;width:1200px;height:521px;background:linear-gradient(100deg,#6b7f36 0%,#8b9a55 25%,#5e5e52 45%,#3a3a3a 70%,#1d1d1d 100%)}
.hero h1{font-family:"Roboto Condensed",sans-serif;font-weight:700;color:#fff;font-size:44px;line-height:60px;text-shadow:0 2px 4px rgba(0,0,0,.4)}
.hero .sub{font-family:"Roboto Condensed",sans-serif;font-weight:700;color:#fff;font-size:20px}
.slide-arrow{width:36px;height:36px;border-radius:50%;background:rgba(0,0,0,.55);display:flex;align-items:center;justify-content:center}
.btn{display:flex;align-items:center;background:var(--gold);color:#fff;font-size:15px;border-radius:2px;overflow:hidden}
.btn span{flex:1;padding-left:16px}
.btn i{width:48px;height:100%;background:var(--gold-dark);display:flex;align-items:center;justify-content:center}

/* welcome */
.welcome{top:690px;left:0;width:1200px;height:199px;background:var(--soft)}
.welcome h2{font-weight:400;font-size:28px;color:#333}
.welcome p{font-size:11.5px;line-height:21px;color:#555}

/* sections */
.section-title{font-size:23px;font-weight:400;color:#333;letter-spacing:.5px}
.car{width:267px;background:#fff;border:1px solid #eee}
.car .photo{height:154px}
.car .label{height:40px;line-height:40px;text-align:center;background:#f4f4f4;font-size:16px;color:#444;position:relative}
.car .label:before{content:"";position:absolute;left:126px;top:-8px;border:8px solid transparent;border-top:0;border-bottom-color:#f4f4f4}
.car .body{height:106px;text-align:center;padding-top:20px}
.car .price{color:var(--price);font-size:16px}
.car .desc{font-size:11px;line-height:20px;color:#777;margin-top:6px}
.car .more{height:36px;line-height:36px;text-align:center;background:#f7f7f7;color:var(--price);font-size:13px}
.car-shadow{width:200px;height:14px;border-radius:50%;background:radial-gradient(ellipse at center,rgba(0,0,0,.28),rgba(0,0,0,0) 70%)}

.finder{top:1372px;left:0;width:1200px;height:257px;background:linear-gradient(#2a2a2a,#111 60%,#2a2a2a)}
.finder h2{font-size:28px;font-weight:700;color:#fff;letter-spacing:.5px}
.select{height:41px;background:#fff;font-size:12px;color:#444;padding-left:18px;line-height:41px}
.select:after{content:"";position:absolute;right:14px;top:17px;border:6px solid transparent;border-top:8px solid #777;border-bottom:0}
.find-btn{left:849px;top:1508px;width:180px;height:42px;border-radius:21px;background:linear-gradient(#f2c21b,#d8a400);color:#fff;font-size:22px;font-weight:600;text-align:center;line-height:42px}

.post{width:270px;height:225px;background:#fff;border:1px solid #eee;padding:16px 17px}
.post .photo{height:190px;position:relative}
.date{position:absolute;right:0;bottom:0;width:62px;background:#fff;text-align:center}
.date b{display:block;font-size:30px;line-height:42px;color:#555;font-weight:700}
.date em{display:block;background:var(--gold);color:#fff;font-style:normal;font-size:10px;line-height:18px}
.post-meta{width:270px;padding-left:17px}
.post-meta h3{font-size:14px;font-weight:400;color:#333}
.post-meta p{font-size:11px;line-height:20px;color:#666;margin-top:8px}
.post-meta a{display:flex;align-items:center;gap:10px;font-size:10px;color:#555;margin-top:8px;text-decoration:none}
.dot-arrow{width:14px;height:14px;border-radius:50%;background:var(--gold);display:flex;align-items:center;justify-content:center}

/* footer */
.footer{top:2081px;left:0;width:1200px;height:111px;background:var(--soft);border-top:1px solid var(--line)}
.copy{left:172px;top:2112px;font-size:11px;color:#444}
.foot-links{left:172px;top:2146px;font-size:11px;color:#333}
.foot-links span{color:#888;margin:0 7px}
.news-title{left:754px;top:2102px;font-size:15px;color:var(--red)}
.news-input{left:754px;top:2133px;width:186px;height:32px;background:#fff;border:1px solid #ddd;font-size:10px;color:#888;line-height:30px;padding-left:14px}
.subscribe{left:952px;top:2133px;width:77px;height:31px;background:var(--gold);color:#fff;font-size:12px;text-align:center;line-height:31px;border-radius:2px}
</style>
</head>
<body>

<header class="abs header">
  <div class="abs brand"><span class="brand-dot"></span>SOLVIK UTLEIE</div>
  <div class="abs lang">Languages <span class="flag"></span>
    <svg width="8" height="12" viewBox="0 0 8 12"><path d="M1 4 4 1 7 4M1 8l3 3 3-3" fill="none" stroke="#555" stroke-width="1.5"/></svg>
  </div>
  <svg class="abs phone-ico" width="42" height="38" viewBox="0 0 42 38">
    <path d="M8 8c-4 4 0 14 8 21s15 9 18 5l-5-6-4 2c-3-1-8-6-9-9l2-4-6-6z" fill="#777"/>
    <circle cx="28" cy="13" r="10" fill="#fff" stroke="#777" stroke-width="2"/>
    <text x="28" y="17" font-size="10" font-family="Open Sans,sans-serif" text-anchor="middle" fill="#555" font-weight="700">24</text>
  </svg>
  <div class="abs phone-txt">Spørsmål? Ring oss<br>+ 40 12 34 56</div>
</header>

<nav class="abs nav">
  <a class="active" href="#">HOME</a>
  <a style="left:278px" href="#">OUR FLEET</a>
  <a style="left:397px" href="#">SERVICES</a>
  <a style="left:506px" href="#">BLOG</a>
  <a style="left:590px" href="#">PAGE TEMPLATES</a>
  <a style="left:753px" href="#">ABOUT US</a>
  <a style="left:869px" href="#">LOGIN</a>
  <a style="left:959px" href="#">CONTACT</a>
</nav>

<section class="abs hero" role="img" aria-label="Photo of a car driving fast past a green roadside, motion blurred">
  <div class="abs center" style="top:100px"><h1>UT I DET FRI!<br>LEKRE PERSONBILER</h1></div>
  <div class="abs center sub" style="top:230px">TIL EN HELT OVERKOMMELIG PENGE!</div>
  <svg class="abs" style="left:559px;top:288px" width="66" height="66" viewBox="0 0 66 66">
    <circle cx="33" cy="33" r="33" fill="rgba(255,255,255,.35)"/>
    <path d="M26 20 48 33 26 46z" fill="rgba(255,255,255,.75)"/>
  </svg>
  <div class="abs btn" style="left:516px;top:382px;width:168px;height:40px"><span>RENT A CAR</span><i><svg width="10" height="14" viewBox="0 0 10 14"><path d="M2 1l6 6-6 6" fill="none" stroke="#fff" stroke-width="2.5"/></svg></i></div>
  <div class="abs slide-arrow" style="left:57px;top:243px"><svg width="10" height="14"><path d="M8 1 2 7l6 6" fill="none" stroke="#ccc" stroke-width="2"/></svg></div>
  <div class="abs slide-arrow" style="left:1111px;top:243px"><svg width="10" height="14"><path d="M2 1l6 6-6 6" fill="none" stroke="#ccc" stroke-width="2"/></svg></div>
</section>

<section class="abs welcome">
  <div class="abs center" style="top:22px"><h2>Welcome to Solvikbyen Car</h2></div>
  <div class="abs center" style="top:67px"><p>Solvik utleie er en bilpark på Strandvik, og leier ut varebiler og personbiler til deg som trenger en ekstrabil til flytting, ferie, bytur eller hva det måtte<br>være. Vi er uslåelige på service, og mest sannsynlig også på pris. Og du kan stole på at bilen du får fra oss er både ren og pen!</p></div>
  <div class="abs btn" style="left:516px;top:129px;width:168px;height:37px"><span>Register Now</span><i><svg width="20" height="20" viewBox="0 0 20 20"><circle cx="10" cy="10" r="8.5" fill="none" stroke="#fff" stroke-width="1.8"/><path d="M10 5v10M5 10h10" stroke="#fff" stroke-width="1.8"/></svg></i></div>
</section>

<div class="abs center section-title" style="top:922px">FEATURED CARS</div>

<article class="abs car" style="left:173px;top:984px">
  <div class="photo" role="img" aria-label="Photo of a red sports coupe at sunset" style="background:linear-gradient(#b06a3a,#3b2a24 60%,#1a1414)"></div>
  <div class="label">Varebilen</div>
  <div class="body"><div class="price">Pris per døgn&nbsp; kr 600</div><div class="desc">Lorem ipsum dolor sit amet, consectetur<br>adipiscing elit, sed do eiusmod</div></div>
  <div class="more">Read More &nbsp;&nbsp;→</div>
</article>
<article class="abs car" style="left:468px;top:984px">
  <div class="photo" role="img" aria-label="Photo of a red sedan on a blurred track" style="background:linear-gradient(120deg,#6d6f77,#c9c9cc 45%,#7a2226 60%,#3f3f44)"></div>
  <div class="label">Varebilen</div>
  <div class="body"><div class="price">Pris per døgn&nbsp; kr 600</div><div class="desc">Lorem ipsum dolor sit amet, consectetur<br>adipiscing elit, sed do eiusmod</div></div>
  <div class="more">Read More &nbsp;&nbsp;→</div>
</article>
<article class="abs car" style="left:763px;top:984px">
  <div class="photo" role="img" aria-label="Photo of a red convertible on a race track" style="background:linear-gradient(#6b8fbf,#b9cbe0 45%,#9b2a31 62%,#555 80%)"></div>
  <div class="label">Varebilen</div>
  <div class="body"><div class="price">Pris per døgn&nbsp; kr 600</div><div class="desc">Lorem ipsum dolor sit amet, consectetur<br>adipiscing elit, sed do eiusmod</div></div>
  <div class="more">Read More &nbsp;&nbsp;→</div>
</article>
<div class="abs car-shadow" style="left:206px;top:1322px"></div>
<div class="abs car-shadow" style="left:501px;top:1322px"></div>
<div class="abs car-shadow" style="left:796px;top:1322px"></div>

<section class="abs finder" role="img" aria-label="Photo of a dark parking garage">
  <div class="abs center" style="top:58px"><h2>FIND A RENT CAR</h2></div>
</section>
<div class="abs select" style="left:172px;top:1508px;width:260px">Select a Make</div>
<div class="abs select" style="left:499px;top:1508px;width:328px">Select Car Model</div>
<div class="abs find-btn">FIND IT</div>

<div class="abs center section-title" style="top:1657px">BLOG POST</div>

<article class="abs post" style="left:172px;top:1711px">
  <div class="photo" role="img" aria-label="Photo of a red convertible on a race track" style="background:linear-gradient(#4f79b8,#aec4de 45%,#9b2a31 60%,#4a4a4a 80%)"><div class="date"><b>23</b><em>OCTOBER</em></div></div>
</article>
<article class="abs post" style="left:468px;top:1711px">
  <div class="photo" role="img" aria-label="Photo of a red coupe under an evening sky" style="background:linear-gradient(#6c7fa8,#d4c7c9 50%,#8c1f2a 70%,#555)"><div class="date"><b>23</b><em>OCTOBER</em></div></div>
</article>
<article class="abs post" style="left:759px;top:1711px">
  <div class="photo" role="img" aria-label="Photo of a red SUV on a forest road" style="background:linear-gradient(#9aa35a,#a23026 45%,#6e1b18 70%,#4a4a3a)"><div class="date"><b>23</b><em>OCTOBER</em></div></div>
</article>

<div class="abs post-meta" style="left:172px;top:1947px"><h3>Phasellus commodo</h3><p>Sed ut perspiciatis unde omnis iste natus<br>error sit voluptatem accusantium doloremque</p><a href="#"><span class="dot-arrow"><svg width="6" height="8"><path d="M1 1l4 3-4 3" fill="none" stroke="#fff" stroke-width="1.5"/></svg></span>Read Article</a></div>
<div class="abs post-meta" style="left:468px;top:1947px"><h3>Phasellus commodo</h3><p>Sed ut perspiciatis unde omnis iste natus<br>error sit voluptatem accusantium doloremque</p><a href="#"><span class="dot-arrow"><svg width="6" height="8"><path d="M1 1l4 3-4 3" fill="none" stroke="#fff" stroke-width="1.5"/></svg></span>Read Article</a></div>
<div class="abs post-meta" style="left:759px;top:1947px"><h3>Phasellus commodo</h3><p>Sed ut perspiciatis unde omnis iste natus<br>error sit voluptatem accusantium doloremque</p><a href="#"><span class="dot-arrow"><svg width="6" height="8"><path d="M1 1l4 3-4 3" fill="none" stroke="#fff" stroke-width="1.5"/></svg></span>Read Article</a></div>

<footer class="abs footer"></footer>
<div class="abs copy">©2014 Solvik Utleie , All Rights Reserved.</div>
<div class="abs foot-links">Home<span>|</span>About Us<span>|</span>Blog<span>|</span>Services<span>|</span>Contact Us</div>
<div class="abs news-title">Newsletter Sign Up</div>
<div class="abs news-input">Enter Your Email</div>
<div class="abs subscribe">Subscribe</div>

</body>
</html>
```